NEW Wordpress Website Design for a Dynamic Long Term Healthcare Company in Hawaii

I would like a new website design for my current company, Marlow Health Collective, which has two different brands - Marlow Homecare and Marlow Senior Living. You can see the current website at www.marlowhealth-example.com. The website should be built using Wordpress Software and the Framewise theme. The website should have a local Hawaii island/tropical feel, but look professional for healthcare. I'm looking for something fresh, and want the designer to select colors, styles, etc.

In the Header, on all pages, I would like a menu that includes Home Care, Senior Living, Rates, and About Us.
Under each of the Header Menu Titles, I would like these drop downs included:
Home Care (drop down pages)- Nurse Aide Care, 24-Hour Home Care, Skilled Nursing, Lifestyle Aide, Hospice at Home, Bathing & Meal Service.
Senior Living (drop down pages) - Long-Term Stay, Short-Term Stay.
Rates (drop down page) - Rates.
About Us (drop down pages) - Our Mission, Ohana Talk, About Dana Marlow.

In the footer, on all pages, you should include the address: 248 Pueo Lane, Suite 310, Honolulu, HI 96817. Phone number: 808-555-0172
The footer should also include buttons for a page called Learn, Caregiver Jobs, and each of the service page links to include: Nurse Aide Care, 24-Hour Home Care, Skilled Nursing, Lifestyle Aide, Hospice at Home, Bathing & Meal Service.
Please don't take the current website and redesign a few aspects. I'm looking for a completely different look and feel.

Target Market(s)

40-80 year olds

Industry/Entity Type

Long Term Healthcare

Coding

Coded - Design and coding required

Requirements
Should not have
• Our existing website as a template. We are looking for a complete redesign. Thank you.

```html
<!DOCTYPE html>
<html lang="en">
<head>
<meta charset="utf-8">
<title>Marlow Care – Mobile Landing Page</title>
<link href="https://fonts.googleapis.com/css2?family=Playfair+Display:wght@400;500;600&family=Poppins:wght@400;500;600&display=swap" rel="stylesheet">
<style>
:root{
  --forest:#0c3a10;
  --coral:#f27474;
  --coral-soft:#fde3e3;
  --sky:#3fb3ef;
  --sky-soft:#d9effc;
  --teal:#4a9c95;
  --ink:#222;
  --muted:#3a3a3a;
  --line:#dedede;
  --white:#fff;
}
*{box-sizing:border-box;margin:0;padding:0}
html,body{width:1200px;height:853px;overflow:hidden;background:var(--forest)}
.stage{position:absolute;left:0;top:0;width:1440px;height:1024px;transform:scale(.833333);transform-origin:0 0;font-family:"Poppins",sans-serif;color:var(--ink)}
.abs{position:absolute}
.serif{font-family:"Playfair Display",serif}
.board-title{position:absolute;width:300px;text-align:center;color:var(--white);font-family:"Playfair Display",serif}
.board-title .name{font-size:25px;line-height:1}
.board-title .sub{font-size:18px;margin-top:10px}
.screen{position:absolute;width:238px;overflow:hidden;background:var(--white)}
.photo{position:absolute;left:0;width:238px}
.coral{color:var(--coral)}
.sky{color:var(--sky)}
.heading{position:absolute;left:0;width:238px;text-align:center;font-family:"Playfair Display",serif;font-size:13px;line-height:18px;color:var(--ink)}
.copy{position:absolute;text-align:center;font-size:8.6px;line-height:11.5px;color:var(--muted)}
.glass{position:absolute;background:rgba(255,255,255,.55);border-radius:6px;box-shadow:0 4px 14px rgba(0,0,0,.12)}
.card{position:absolute;background:var(--white);border-radius:5px;box-shadow:0 3px 12px rgba(0,0,0,.08);text-align:center}
.card.coral-edge{border-bottom:4px solid var(--coral)}
.card.sky-edge{border-bottom:4px solid var(--sky)}
.card svg{position:absolute;left:50%;transform:translateX(-50%)}
.card .title{position:absolute;left:0;width:100%;font-family:"Playfair Display",serif;font-size:13px;font-weight:500}
.card .text{position:absolute;left:12px;right:12px;font-size:8.6px;line-height:11.5px;color:var(--muted)}
.btn{position:absolute;border-radius:5px;color:var(--white);font-family:"Playfair Display",serif;font-size:9.5px;font-weight:600;letter-spacing:.3px;text-align:center;box-shadow:0 4px 12px rgba(0,0,0,.12)}
.btn.coral-fill{background:var(--coral)}
.btn.sky-fill{background:var(--sky)}
.field{position:absolute;left:22px;width:194px;height:21px;border:1px solid var(--line);border-radius:3px;background:var(--white);font-size:7.5px;color:#888;padding:5px 6px;line-height:10px}
.field.select::after{content:"";position:absolute;right:6px;top:8px;border-left:3px solid transparent;border-right:3px solid transparent;border-top:4px solid var(--coral)}
.consent{position:absolute;left:22px;width:194px;font-size:5.4px;line-height:7px;color:#555}
.submit{position:absolute;left:22px;width:194px;height:28px;border-radius:4px;background:var(--sky);color:var(--white);font-family:"Playfair Display",serif;font-weight:600;font-size:14px;text-align:center;line-height:28px}
.brand{position:absolute;text-align:center;font-family:"Playfair Display",serif}
.brand i{display:block;margin:0 auto 3px}
.links{position:absolute;font-size:7.3px;line-height:22.8px;color:#333}
.label{position:absolute;left:0;width:100%;text-align:center;font-size:7.5px;font-weight:600;letter-spacing:.6px}
</style>
</head>
<body>
<div class="stage">

  <div class="board-title" style="left:31px;top:52px">
    <div class="name">Marlow Care</div>
    <div class="sub">Mobile View - Landing Page</div>
  </div>
  <div class="board-title" style="left:1107px;top:830px">
    <div class="name">Marlow Care</div>
    <div class="sub">Mobile View - Landing Page</div>
  </div>

  <!-- Screen 1: header, hero and home care services -->
  <section class="screen" style="left:63px;top:169px;height:855px;border-radius:20px 20px 0 0;background:linear-gradient(#fff 0,#fff 380px,var(--coral-soft) 380px,#fff 560px,#fff)">
    <svg class="abs" style="left:12px;top:25px" width="11" height="8" viewBox="0 0 11 8"><path d="M0 1h11M0 4h11M0 7h11" stroke="#222" stroke-width="1.3"/></svg>
    <div class="brand" style="left:66px;top:22px;font-size:7px;color:var(--coral)"><i style="width:8px;height:6px;background:var(--coral)"></i>Marlow</div>
    <div class="brand" style="left:99px;top:14px;font-size:7px;color:#111"><i style="width:8px;height:7px;background:#111"></i>Marlow</div>
    <div class="brand" style="left:137px;top:22px;font-size:7px;color:var(--teal)"><i style="width:8px;height:6px;background:var(--teal)"></i>Marlow</div>
    <div class="abs" style="left:202px;top:17px;width:25px;height:25px;border:1px solid #222;border-radius:5px">
      <svg width="23" height="23" viewBox="0 0 24 24"><path d="M7 5l3 3-2 2c1 2.5 3.5 5 6 6l2-2 3 3-2 2.5c-5.5 0-12-6.5-12-12z" fill="none" stroke="#222" stroke-width="1.2"/></svg>
    </div>
    <div class="abs" style="left:0;top:56px;width:238px;height:3px;background:var(--coral)"></div>
    <div class="photo" role="img" aria-label="Caregiver and senior seated together in a sunlit living room" style="top:59px;height:271px;background:linear-gradient(160deg,#b88a55,#8b5a34 45%,#c9a078 75%,#7a4a2c)"></div>
    <div class="glass" style="left:11px;top:100px;width:216px;height:192px"></div>
    <div class="abs" style="left:0;top:133px;width:238px;text-align:center;font-size:5.5px;letter-spacing:.5px">WELCOME TO</div>
    <div class="heading" style="top:142px;font-size:12.5px;font-weight:600">HAWAII'S CHOICE</div>
    <div class="heading" style="top:160px;font-size:12.5px"><span class="coral">HOMECARE</span> &amp; <span class="sky">SENIOR LIVING</span></div>
    <div class="copy" style="left:20px;width:198px;top:190px;color:#222">Marlow Homecare provides a variety of professional in-home health care services throughout the entire island of Oahu. Marlow Senior Living, a beautiful Adult Residential Care Home, is located on the windward side of Oahu in Kailua.</div>
    <div class="card" style="left:11px;top:335px;width:216px;height:43px;border-bottom:4px solid var(--coral)">
      <span class="abs serif coral" style="left:34px;top:16px;font-size:7.5px">HOMECARE</span>
      <span class="abs serif sky" style="left:128px;top:16px;font-size:7.5px">SENIOR LIVING</span>
    </div>
    <div class="heading" style="top:408px">Comprehensive <span class="coral">Home Care</span> Services<br>with Heart</div>
    <div class="copy" style="left:8px;width:222px;top:455px">From skilled nursing to lifestyle aid, our expert caregivers bring compassionate care into your home, helping you or your loved ones live independently</div>
    <div class="card coral-edge" style="left:33px;top:527px;width:172px;height:126px">
      <svg style="top:10px" width="40" height="28" viewBox="0 0 40 28"><path d="M4 10c6-8 26-8 32 0l-4 12c-8-3-16-3-24 0z" fill="none" stroke="var(--coral)" stroke-width="1.6"/><path d="M20 9v8M16 13h8" stroke="var(--coral)" stroke-width="1.6"/></svg>
      <div class="title coral" style="top:51px">Nurse Aide Care</div>
      <div class="text" style="top:80px">Professional support to assist with daily needs and personal care.</div>
    </div>
    <div class="card coral-edge" style="left:33px;top:678px;width:172px;height:114px">
      <svg style="top:9px" width="30" height="30" viewBox="0 0 30 30"><circle cx="15" cy="15" r="12" fill="none" stroke="var(--coral)" stroke-width="1.6" stroke-dasharray="60 6"/><text x="15" y="19" text-anchor="middle" font-family="Poppins,sans-serif" font-size="10" font-weight="600" fill="var(--coral)">24</text></svg>
      <div class="title coral" style="top:50px">24-Hour Home Care</div>
      <div class="text" style="top:78px">Round-the-clock assistance tailored to meet all your needs.</div>
    </div>
    <div class="card" style="left:33px;top:817px;width:172px;height:60px">
      <svg style="top:10px" width="26" height="30" viewBox="0 0 26 30"><rect x="8" y="2" width="10" height="11" rx="3" fill="none" stroke="var(--coral)" stroke-width="1.6"/><path d="M3 29c0-8 4-12 10-12s10 4 10 12z" fill="none" stroke="var(--coral)" stroke-width="1.6"/><path d="M13 21v5M10.5 23.5h5" stroke="var(--coral)" stroke-width="1.4"/></svg>
    </div>
  </section>

  <!-- Screen 2: assessment call to action and senior living gallery -->
  <section class="screen" style="left:332px;top:0;height:1024px;background:linear-gradient(#fff 840px,var(--sky-soft) 1024px)">
    <div class="abs" style="left:0;top:0;width:238px;height:110px;background:var(--coral-soft)"></div>
    <div class="btn coral-fill" style="left:27px;top:26px;width:184px;height:34px;line-height:34px">SCHEDULE CARE ASSESSMENT</div>
    <div class="photo" role="img" aria-label="Caregiver serving a meal to seniors at a dining table" style="top:110px;height:243px;background:linear-gradient(150deg,#8a4a2c,#c98b57 40%,#e9d6b8 70%,#6d3b24)"></div>
    <div class="photo" role="img" aria-label="Nurse in blue scrubs helping a senior sit up in bed" style="top:353px;height:244px;background:linear-gradient(200deg,#d9cf6b,#e9dc8a 35%,#4fa3b7 65%,#a8552f)"></div>
    <div class="photo" role="img" aria-label="Caregiver and resident sharing a moment on a living room sofa" style="top:597px;height:243px;background:linear-gradient(160deg,#c9b48a,#7a5a3c 40%,#3f78b8 65%,#9c6a48)"></div>
    <div class="heading" style="top:889px">Aloha in Every Moment of<br><span class="sky">Senior Living</span></div>
    <div class="copy" style="left:8px;width:222px;top:937px">Our senior living options offer comfort, community, and care in a tropical paradise. Whether for short-term or long-term stays, we ensure a home-like experience.</div>
    <div class="card" style="left:11px;top:1010px;width:216px;height:40px"></div>
  </section>

  <!-- Screen 3: senior living stays -->
  <section class="screen" style="left:601px;top:0;height:1024px;background:linear-gradient(#fff 168px,#fff 330px,var(--sky-soft) 780px)">
    <div class="photo" role="img" aria-label="Caregiver and resident seated on a leather sofa" style="top:0;height:168px;background:linear-gradient(160deg,#c9b48a,#7a5a3c 40%,#3f78b8 65%,#9c6a48)"></div>
    <div class="heading" style="top:219px">Aloha in Every Moment of<br><span class="sky">Senior Living</span></div>
    <div class="copy" style="left:8px;width:222px;top:265px">Our senior living options offer comfort, community, and care in a tropical paradise. Whether for short-term or long-term stays, we ensure a home-like experience.</div>
    <div class="card sky-edge" style="left:11px;top:338px;width:216px;height:153px">
      <svg style="top:10px" width="40" height="28" viewBox="0 0 40 28"><path d="M4 10c6-8 26-8 32 0l-4 12c-8-3-16-3-24 0z" fill="none" stroke="var(--sky)" stroke-width="1.6"/><path d="M20 9v8M16 13h8" stroke="var(--sky)" stroke-width="1.6"/></svg>
      <div class="title sky" style="top:51px">Long-Term Stay</div>
      <div class="text" style="top:80px">A welcoming community for those who need ongoing support</div>
    </div>
    <div class="card sky-edge" style="left:11px;top:516px;width:216px;height:153px">
      <svg style="top:9px" width="30" height="30" viewBox="0 0 30 30"><circle cx="15" cy="15" r="12" fill="none" stroke="var(--sky)" stroke-width="1.6" stroke-dasharray="60 6"/><text x="15" y="19" text-anchor="middle" font-family="Poppins,sans-serif" font-size="10" font-weight="600" fill="var(--sky)">24</text></svg>
      <div class="title sky" style="top:51px">Short-Term Stay</div>
      <div class="text" style="top:80px">Round-the-clock assistance tailored to meet all your needs.</div>
    </div>
    <div class="btn sky-fill" style="left:60px;top:695px;width:118px;height:36px;line-height:36px">SCHEDULE TOUR</div>
    <div class="photo" role="img" aria-label="Caregiver walking with a resident using a walker in a tropical garden" style="top:780px;height:244px;background:linear-gradient(180deg,#d9e6e0,#5f8f4a 35%,#3f6b34 60%,#b8b4ac)"></div>
  </section>

  <!-- Screen 4: about and consultation form -->
  <section class="screen" style="left:870px;top:0;height:1024px">
    <div class="photo" role="img" aria-label="Blurred close-up of a nurse with a stethoscope" style="top:0;height:527px;background:linear-gradient(160deg,#eef3f4,#9fc6cf 35%,#5f8592 60%,#d7e6ea 85%,#fff)"></div>
    <div class="glass" style="left:11px;top:148px;width:216px;height:230px;background:rgba(160,190,196,.55)"></div>
    <div class="heading" style="top:182px">Dedicated to Serving<br>Hawaii's Ohana</div>
    <div class="copy" style="left:40px;width:158px;top:241px;color:#222">Founded by Dana Marlow, our mission is to provide compassionate, high-quality care to families across Hawaii.</div>
    <div class="btn sky-fill" style="left:61px;top:311px;width:116px;height:36px;line-height:36px">SCHEDULE TOUR</div>
    <div class="photo" role="img" aria-label="Softly blurred bright clinic interior" style="top:527px;height:443px;background:linear-gradient(170deg,#e8efe9,#c2d3d8 40%,#9aa8ad 75%,#cfd6d8)"></div>
    <div class="glass" style="left:11px;top:555px;width:216px;height:378px;background:rgba(255,255,255,.35)"></div>
    <div class="heading" style="top:577px">Schedule a <span class="sky">complimentary</span><br>Care Consultation</div>
    <div class="field" style="top:639px">Name*</div>
    <div class="field" style="top:667px">Email*</div>
    <div class="field" style="top:695px">Phone*</div>
    <div class="field select" style="top:723px">How Can We Help?</div>
    <div class="field" style="top:752px;height:46px;padding-top:18px">Questions/comments</div>
    <div class="field" style="top:805px">Where did you hear about is?</div>
    <div class="field select" style="top:833px">May We Email You About This?</div>
    <div class="consent" style="top:871px">You agree to receive future emails and understand you may opt-out at any time</div>
    <div class="submit" style="top:894px">Submit</div>
    <div class="abs" style="left:0;top:970px;width:238px;height:4px;background:var(--coral)"></div>
    <i class="abs" style="left:34px;top:1020px;width:20px;height:4px;background:var(--coral)"></i>
    <i class="abs" style="left:108px;top:1014px;width:20px;height:10px;background:#111;border-radius:3px 3px 0 0"></i>
  </section>

  <!-- Screen 5: form end and footer -->
  <section class="screen" style="left:1139px;top:0;height:746px;border-radius:0 0 20px 20px">
    <div class="photo" role="img" aria-label="Softly blurred clinic interior" style="top:0;height:270px;background:linear-gradient(170deg,#c9cfcf,#a9b3b5 50%,#d6d0c8)"></div>
    <div class="glass" style="left:11px;top:-10px;width:216px;height:242px;background:rgba(255,255,255,.3)"></div>
    <div class="field" style="top:-7px">Phone*</div>
    <div class="field select" style="top:22px">How Can We Help?</div>
    <div class="field" style="top:50px;height:46px;padding-top:18px">Questions/comments</div>
    <div class="field" style="top:103px">Where did you hear about is?</div>
    <div class="field select" style="top:131px">May We Email You About This?</div>
    <div class="consent" style="top:169px">You agree to receive future emails and understand you may opt-out at any time</div>
    <div class="submit" style="top:192px">Submit</div>
    <div class="abs" style="left:0;top:270px;width:238px;height:4px;background:var(--coral)"></div>

    <div class="brand" style="left:12px;top:320px;width:64px;font-size:17px;color:var(--coral)"><i style="width:20px;height:16px;background:var(--coral)"></i>Marlow</div>
    <div class="brand" style="left:86px;top:310px;width:66px;font-size:17px;color:#111"><i style="width:20px;height:18px;background:#111"></i>Marlow</div>
    <div class="brand" style="left:160px;top:320px;width:66px;font-size:17px;color:var(--teal)"><i style="width:18px;height:16px;background:var(--teal)"></i>Marlow</div>

    <div class="label" style="top:419px">LINKS</div>
    <div class="links" style="left:35px;top:443px">Home<br>Contact<br>Learn<br>Caregiver Jobs<br>Privacy Policy</div>
    <div class="links" style="left:113px;top:443px">Nurse Aide Care<br>24-Hour Home Care<br>Skilled Nursing<br>Lifestyle Aide<br>Hospice at Home<br>Bathing &amp; Meal Service</div>
    <div class="label" style="top:608px">CONTACT</div>
    <div class="abs" style="left:0;top:637px;width:238px;text-align:center;font-size:7.3px">808-555-0172</div>
    <div class="abs" style="left:0;top:654px;width:238px;text-align:center;font-size:5.6px">248 Pueo Lane, Suite 310, Honolulu, HI 96817</div>
    <i class="abs" style="left:96px;top:678px;width:7px;height:7px;border-radius:50%;background:#222"></i>
    <i class="abs" style="left:114px;top:678px;width:7px;height:7px;border-radius:50%;background:#222"></i>
    <i class="abs" style="left:133px;top:678px;width:7px;height:7px;border-radius:50%;background:#222"></i>
    <div class="abs" style="left:0;top:707px;width:238px;text-align:center;font-size:3.8px;color:#555">© 2024 Marlow Health Collective. All Rights Reserved</div>
  </section>

</div>
</body>
</html>
```